Payment company requires web design

We need a web design for a new company based in Singapore.

The company focuses on providing 2 key products: 1) an alternative payment option (i.e. like quib or trelloquin options) on the traditional checkout process 2) a replacement/outsource of a merchants payment page. Key in the UX flow is a end customer dashboard that manages all payments.

We look to provide a simple, fluid and easy to use payment process. The dashboard is minimalistic that allows easy navigation, review of transactions and all available options through gamification.

The final design should communicate ease of use, flexibility and transparency.

Target Market(s)

The value is for the merchant - retail/travel/insurance companies. However its the merchant's end customers that are the target and who the UX is built for.

Industry/Entity Type

It Company

Logo Text

zelnar

Number of Pages Required

5+ page

Colors
ec1f27

Requirements
Must have
• 7 pages mimicking UX flow
• payment page * 2 - 1) alternative payment type 2) outsource of merchants payment page to our business
• our landing page
• end customer verification page
• end customer registration
• customer dashboard
• UX flow in attached file
Nice to have
• open to ideas
• have asked for the logo to be added
• logo to have the colour red (chinese for prosperity)
• the company is all about flexibility, transparency in personal finance management with the option of instalment payments

```html
<!DOCTYPE html>
<html lang="en">
<head>
<meta charset="utf-8">
<title>Zelnar — Dashboard</title>
<link href="https://fonts.googleapis.com/css2?family=Lato:wght@300;400;700&display=swap" rel="stylesheet">
<style>
:root{
  --red:#ec1f27;
  --green:#3f8a1c;
  --ink:#333;
  --muted:#777;
  --line:#e4e4e4;
  --grey-dot:#cfcfcf;
  --canvas:#ebebeb;
  --band:#f5f5f5;
  --card:#fff;
  --pink:#fdeeee;
}
*{box-sizing:border-box;margin:0;padding:0}
html,body{width:1200px;height:854px;overflow:hidden}
body{font-family:'Lato',sans-serif;color:var(--ink);background:var(--canvas);position:relative;font-size:11px}
.sidebar{position:absolute;left:0;top:0;width:194px;height:854px;background:var(--card)}
.brand{position:absolute;left:50px;top:11px;display:flex;align-items:center;gap:5px;color:var(--red);font-weight:700;font-size:21px}
.brand .mark{width:16px;height:16px;background:var(--red)}
.profile-photo{position:absolute;left:61px;top:68px;width:76px;height:76px;border-radius:50%;border:3px solid #f2f2f2;background:radial-gradient(circle at 50% 45%,#c9a58e,#6b4b3c)}
.profile-name{position:absolute;top:154px;width:194px;text-align:center;font-size:13px;letter-spacing:.3px}
.profile-place{position:absolute;top:172px;width:194px;text-align:center;font-size:10px;color:var(--muted)}
.nav{position:absolute;top:214px;left:0;width:194px;list-style:none}
.nav li{height:37px;border-bottom:1px solid var(--line);display:flex;align-items:center;padding-left:30px;gap:8px;font-size:10.5px;letter-spacing:.4px}
.nav li.active{background:var(--red);color:#fff;border-color:var(--red)}
.nav svg{width:10px;height:10px}
.topbar{position:absolute;left:194px;top:0;width:1006px;height:47px;background:var(--band);border-bottom:1px solid #ddd}
.burger{position:absolute;left:14px;top:19px;width:9px;height:8px;border-top:2px solid #333;border-bottom:2px solid #333}
.burger::after{content:"";position:absolute;left:0;top:1px;width:9px;height:2px;background:#333}
.gear-box{position:absolute;left:838px;top:0;width:40px;height:47px;background:#ececec;display:flex;align-items:center;justify-content:center}
.user-chip{position:absolute;left:889px;top:10px;display:flex;align-items:center;gap:10px;font-size:10.5px}
.user-chip .avatar{width:28px;height:28px;border-radius:50%;background:radial-gradient(circle at 50% 45%,#c9a58e,#6b4b3c)}
.page-head{position:absolute;left:194px;top:47px;width:1006px;height:69px;background:var(--band)}
.page-title{position:absolute;left:12px;top:8px;font-weight:300;font-size:46px;color:#bbb;letter-spacing:.5px}
.search{position:absolute;left:903px;top:21px;width:84px;height:29px;border:1px solid var(--red);border-radius:15px}
.search svg{position:absolute;right:9px;top:8px}
.card{position:absolute;background:var(--card)}
.card-title{position:absolute;left:12px;top:14px;font-size:10px;letter-spacing:.4px}
.chev{position:absolute;right:14px;top:17px;width:5px;height:5px;border-right:1px solid #333;border-bottom:1px solid #333;transform:rotate(45deg)}
.credit{left:206px;top:147px;width:288px;height:327px}
.credit svg.ring{position:absolute;left:60px;top:62px}
.credit .pct{position:absolute;left:0;width:288px;top:128px;text-align:center;font-weight:300;font-size:40px;color:#555}
.credit .totals{position:absolute;left:0;top:265px;width:288px;height:62px;border-top:1px solid var(--line);display:flex}
.totals div{flex:1;padding:8px 12px}
.totals div+div{border-left:1px solid var(--line);text-align:right}
.totals b{display:block;font-weight:300;font-size:26px;color:#444}
.totals div+div b{color:var(--green)}
.totals span{font-size:10px;color:var(--muted)}
.repay{left:506px;top:147px;width:688px;height:327px}
.table{position:absolute;left:12px;right:13px;font-size:10px}
.table .row{display:grid;align-items:center;border-bottom:1px solid var(--line);height:38px;padding-left:12px;color:#666}
.table .head{color:#444;letter-spacing:.3px}
.repay .table{top:42px}
.repay .row{grid-template-columns:122px 138px 157px 119px 1fr}
.dots{display:flex;gap:1.6px}
.dots i{width:9px;height:9px;border-radius:50%;background:var(--grey-dot)}
.dots i.r{background:var(--red)}.dots i.g{background:var(--green)}
.view-all{position:absolute;right:25px;color:var(--red);font-size:10.5px}
.monthly{left:206px;top:487px;width:288px;height:285px}
.monthly .rule{position:absolute;left:0;right:0;top:37px;border-top:1px solid var(--line)}
.monthly svg{position:absolute;left:0;top:0}
.purchases{left:506px;top:487px;width:438px;height:285px}
.purchases .table{top:44px;right:13px}
.purchases .row{grid-template-columns:158px 116px 1fr 20px}
.pc-low{color:var(--red)}.pc-full{color:var(--green)}
.arrow{width:5px;height:5px;border-right:1px solid #333;border-top:1px solid #333;transform:rotate(45deg)}
.support{left:956px;top:487px;width:238px;height:285px}
.msg{position:absolute;left:12px;width:213px;height:45px;background:var(--pink);display:flex;align-items:center;gap:10px;padding-left:9px;font-size:10px;color:#555}
.msg .agent{width:28px;height:28px;border-radius:50%;background:var(--red)}
.msg-user{position:absolute;left:12px;top:103px;width:213px;display:flex;align-items:center;justify-content:flex-end;gap:8px;font-size:10px;color:#555;text-align:right;line-height:1.2}
.msg-user .avatar{width:28px;height:28px;border-radius:50%;background:radial-gradient(circle at 50% 45%,#c9a58e,#6b4b3c);flex:none}
.composer{position:absolute;left:12px;top:244px;width:213px;height:29px;border:1px solid var(--red);border-radius:15px;padding-left:10px;display:flex;align-items:center;font-size:10px;color:#888}
.composer svg{position:absolute;right:10px;top:8px}
.footer{position:absolute;left:206px;top:802px;width:988px;border-top:1px solid #d6d6d6}
.social{position:absolute;left:0;top:20px;display:flex;gap:14px;font-size:9px;color:#555}
.social span{display:flex;align-items:center;gap:4px}
.social span::before{content:"";width:5px;height:5px;border-radius:50%;background:#555}
.copyright{position:absolute;right:0;top:20px;font-size:10.5px;color:#666}
.copyright em{font-style:normal;color:var(--red)}
</style>
</head>
<body>
<aside class="sidebar">
  <div class="brand"><span class="mark"></span>zelnar</div>
  <div class="profile-photo" role="img" aria-label="Profile photo of the account holder"></div>
  <div class="profile-name">Malee Tanaporn</div>
  <div class="profile-place">Novena, Singapore</div>
  <ul class="nav">
    <li class="active"><svg viewBox="0 0 10 10" fill="none" stroke="#fff"><path d="M1 5 5 1l4 4M2 4v5h6V4"/></svg>DASHBOARD</li>
    <li><svg viewBox="0 0 10 10" fill="none" stroke="#333"><circle cx="5" cy="3" r="2"/><path d="M1 9.5c0-2.5 8-2.5 8 0"/></svg>PROFILE</li>
    <li><svg viewBox="0 0 10 10" fill="none" stroke="#333"><rect x="1" y="3" width="8" height="6"/><path d="M2 3l5-2 1 2"/></svg>REPAYMENTS</li>
    <li><svg viewBox="0 0 10 10" fill="none" stroke="#333"><circle cx="5" cy="5" r="1.5"/><circle cx="5" cy="5" r="3.7" stroke-dasharray="1.5 1"/></svg>SETTINGS</li>
  </ul>
</aside>

<header class="topbar">
  <div class="burger"></div>
  <div class="gear-box"><svg width="10" height="10" viewBox="0 0 10 10"><circle cx="5" cy="5" r="3.5" fill="none" stroke="#222" stroke-width="2.4" stroke-dasharray="1.6 1"/><circle cx="5" cy="5" r="2.3" fill="#222"/><circle cx="5" cy="5" r=".9" fill="#ececec"/></svg></div>
  <div class="user-chip"><div class="avatar" role="img" aria-label="Account holder avatar"></div>Hi, Malee <svg width="7" height="5" viewBox="0 0 7 5"><path d="M1 1l2.5 2.5L6 1" fill="none" stroke="#333"/></svg></div>
</header>

<div class="page-head">
  <h1 class="page-title">Dashboard</h1>
  <div class="search"><svg width="11" height="11" viewBox="0 0 11 11" fill="none" stroke="#ec1f27" stroke-width="1.6"><circle cx="4.5" cy="4.5" r="3.3"/><path d="M7 7l3 3"/></svg></div>
</div>

<section class="card credit">
  <h2 class="card-title">CREDIT STATUS</h2><span class="chev"></span>
  <svg class="ring" width="168" height="168" viewBox="0 0 168 168">
    <circle cx="84" cy="84" r="81" fill="none" stroke="#f0f0f0" stroke-width="1"/>
    <circle cx="84" cy="84" r="81" fill="none" stroke="#3f8a1c" stroke-width="5" stroke-dasharray="381.7 127.2" transform="rotate(-90 84 84)"/>
  </svg>
  <div class="pct">24%</div>
  <div class="totals">
    <div><b>$600</b><span>Credit Used</span></div>
    <div><b>$2500</b><span>Credit Limit</span></div>
  </div>
</section>

<section class="card repay">
  <h2 class="card-title">REPAYMENTS</h2>
  <div class="table">
    <div class="row head"><span>PAYMENT #</span><span>DATE</span><span>MERCHANT</span><span>AMOUNT</span><span>INSTALLMENTS LEFT</span></div>
    <div class="row"><span>#43</span><span>Dec 08, 2016</span><span>Lorem ipsum dolor</span><span>$500.00</span><span class="dots"><i class="r"></i><i class="r"></i><i class="r"></i><i></i><i></i></span></div>
    <div class="row"><span>#42</span><span>Dec 03, 2016</span><span>Lorem ipsum dolor</span><span>$500.00</span><span class="dots"><i class="r"></i><i class="r"></i><i></i><i></i><i></i></span></div>
    <div class="row"><span>#41</span><span>Nov 28, 2016</span><span>Lorem ipsum dolor</span><span>$500.00</span><span class="dots"><i class="r"></i><i class="r"></i><i class="r"></i><i class="r"></i><i></i></span></div>
    <div class="row"><span>#40</span><span>Nov 15, 2016</span><span>Lorem ipsum dolor</span><span>$500.00</span><span class="dots"><i class="g"></i><i class="g"></i><i class="g"></i><i class="g"></i><i class="g"></i></span></div>
    <div class="row"><span>#39</span><span>Oct 30, 2016</span><span>Lorem ipsum dolor</span><span>$500.00</span><span class="dots"><i class="g"></i><i class="g"></i><i class="g"></i><i class="g"></i><i class="g"></i></span></div>
  </div>
  <a class="view-all" style="top:293px">View All</a>
</section>

<section class="card monthly">
  <h2 class="card-title">MONTHLY REPORT</h2><span class="chev"></span>
  <div class="rule"></div>
  <svg width="288" height="285" viewBox="0 0 288 285" font-family="Lato, sans-serif" font-size="9" fill="#777">
    <circle cx="66" cy="54" r="4" fill="#3f8a1c"/><text x="73" y="57.5" font-size="10" fill="#444">Credit Limit</text>
    <circle cx="164" cy="54" r="4" fill="#ec1f27"/><text x="171" y="57.5" font-size="10" fill="#444">Credit Used</text>
    <g stroke="#e6e6e6">
      <line x1="50" x2="274" y1="101" y2="101"/><line x1="50" x2="274" y1="139" y2="139"/>
      <line x1="50" x2="274" y1="177" y2="177"/><line x1="50" x2="274" y1="215" y2="215"/>
      <line x1="50" x2="274" y1="253" y2="253"/>
    </g>
    <text x="13" y="104">$2000</text><text x="13" y="142">$1500</text><text x="13" y="180">$1000</text>
    <text x="13" y="218">$500</text><text x="13" y="256">$0</text>
    <rect x="82" y="114" width="9" height="42" fill="#3f8a1c"/><rect x="82" y="156" width="9" height="97" fill="#ec1f27"/>
    <rect x="133" y="129" width="9" height="48" fill="#3f8a1c"/><rect x="133" y="177" width="9" height="76" fill="#ec1f27"/>
    <rect x="183" y="102" width="9" height="38" fill="#3f8a1c"/><rect x="183" y="140" width="9" height="113" fill="#ec1f27"/>
    <rect x="233" y="79" width="9" height="130" fill="#3f8a1c"/><rect x="233" y="209" width="9" height="44" fill="#ec1f27"/>
    <text x="80" y="272">Sep</text><text x="128" y="272">Oct</text><text x="179" y="272">Nov</text><text x="229" y="272">Dec</text>
  </svg>
</section>

<section class="card purchases">
  <h2 class="card-title">RECENT PURCHASES</h2><span class="chev"></span>
  <div class="table">
    <div class="row head"><span>MERCHANT</span><span>AMOUNT</span><span>REPAID</span><span></span></div>
    <div class="row"><span>Lorem ipsum dolor</span><span>$175.00</span><span class="pc-low">37%</span><span class="arrow"></span></div>
    <div class="row"><span>Duis autem veleum</span><span>$208.00</span><span class="pc-low">58%</span><span class="arrow"></span></div>
    <div class="row"><span>Claritas est etiam</span><span>$126.00</span><span class="pc-full">100%</span><span class="arrow"></span></div>
    <div class="row"><span>Mirum est notare</span><span>$350.00</span><span class="pc-full">100%</span><span class="arrow"></span></div>
  </div>
  <a class="view-all" style="top:250px">View All</a>
</section>

<section class="card support">
  <h2 class="card-title">LIVE SUPPORT</h2><span class="chev"></span>
  <div class="msg" style="top:44px"><span class="agent"></span>Hey! How can we help?</div>
  <div class="msg-user"><span>I need help understanding my<br>repayment options</span><span class="avatar" role="img" aria-label="Account holder avatar"></span></div>
  <div class="msg" style="top:144px"><span class="agent"></span>Sure</div>
  <div class="composer">Type your message here
    <svg width="12" height="12" viewBox="0 0 12 12"><path d="M1 6 11 1 7 11 6 7z" fill="#ec1f27"/></svg>
  </div>
</section>

<footer class="footer">
  <div class="social"><span>Socia</span><span>Chirpa</span><span>Linkro</span></div>
  <div class="copyright">Copyright © <em>Zelnar</em> 2016</div>
</footer>
</body>
</html>
```